Lantern Hollow Brewing Company New Website with Food Ordering

We need a wordpress-based website for a local brewery & pizza kitchen. The final design will have 6 primary pages: home page, order pizza, our beers, visit us, about us, merch store. The website must integrate with tillpoint for kitchens for online ordering for takeout and delivery. It will also a feature a selection of beers and help customers navigate to the brewery and find hours of operation. The existing website is lanternhollowbrew.example. This is a very old website.

Industry/Entity Type

Brewery and food service

Coding

Coded - Design and coding required

Number of Pages Required

5+ page

Font styles to use
Sans Serif

Requirements
Must have
• ability to integrate seamlessly with tillpoint for kitchens, 21+ age gate
Nice to have
• see attached pdf

```html
<!DOCTYPE html>
<html lang="en">
<head>
<meta charset="utf-8">
<title>Lantern Hollow Brewing Company</title>
<link rel="stylesheet" href="https://fonts.googleapis.com/css2?family=IBM+Plex+Sans:wght@400;500;600&family=Merriweather:wght@700;900&family=Poppins:wght@600&display=swap">
<style>
  :root {
    --brand-red: #c8102e;
    --hero-red: #cc1a3a;
    --ink: #222222;
    --body-text: #3a3a3a;
    --white: #ffffff;
    --black: #000000;
    --footer-rule: #2a2a2a;
    --burst-yellow: #f7c52b;
  }
  * { box-sizing: border-box; margin: 0; padding: 0; }
  html, body { width: 894px; height: 1200px; overflow: hidden; background: var(--white); }
  body { position: relative; font-family: "IBM Plex Sans", Arial, sans-serif; color: var(--ink); }

  .site-header { position: absolute; left: 0; top: 0; width: 894px; height: 85px; background: var(--white); z-index: 3; }
  .main-nav a { position: absolute; top: 40px; font-size: 11.5px; color: var(--ink); text-decoration: none; letter-spacing: .2px; }
  .main-nav a.is-active { color: var(--brand-red); }
  .search-icon { position: absolute; left: 795px; top: 39px; }

  .brand-tab { position: absolute; left: 384px; top: 8px; width: 126px; height: 108px; background: var(--white); z-index: 4; display: flex; align-items: center; justify-content: center; }
  .brand-tab .brand-name { font-family: "Merriweather", Georgia, serif; font-weight: 900; font-size: 17px; line-height: 1.2; color: var(--brand-red); text-align: center; }

  .hero { position: absolute; left: 0; top: 85px; width: 894px; height: 447px; overflow: hidden; }
  .hero-photo { position: absolute; inset: 0; background: linear-gradient(135deg, #7a2a22 0%, #a33a2c 35%, #c9835a 55%, #6b2b26 80%, #3a1a18 100%); }
  .hero-panel { position: absolute; inset: 0; background: var(--hero-red); clip-path: polygon(485px 0, 894px 0, 894px 447px, 409px 447px); }
  .hero-title { position: absolute; left: 493px; top: 150px; width: 350px; font-family: "Merriweather", Georgia, serif; font-weight: 900; font-size: 31px; line-height: 46px; color: var(--white); letter-spacing: .3px; }
  .hero-actions a { position: absolute; top: 311px; height: 36px; border: 1.5px solid var(--white); border-radius: 2px; font-family: "Merriweather", Georgia, serif; font-weight: 700; font-size: 11px; color: var(--white); text-decoration: none; display: flex; align-items: center; justify-content: center; }
  .hero-actions a.is-primary { background: var(--white); color: var(--brand-red); }
  .slider-dots span { position: absolute; left: 848px; width: 8px; height: 8px; border-radius: 50%; background: var(--white); }
  .slider-dots span.is-current { background: transparent; border: 1.5px solid var(--white); }
  .promo-badge { position: absolute; left: 694px; top: 44px; width: 112px; height: 80px; border-radius: 50%; background: var(--burst-yellow); display: flex; align-items: center; justify-content: center; font-family: "Merriweather", Georgia, serif; font-weight: 900; font-size: 10px; color: var(--brand-red); }

  .intro { position: absolute; left: 0; top: 532px; width: 894px; height: 399px; }
  .intro-title { position: absolute; left: 83px; top: 60px; font-family: "Merriweather", Georgia, serif; font-weight: 900; font-size: 21px; color: var(--brand-red); }
  .intro-text { position: absolute; left: 83px; top: 108px; width: 364px; font-size: 11px; line-height: 19.2px; color: var(--body-text); text-align: justify; }
  .intro-actions a { position: absolute; top: 271px; height: 36px; border: 1.5px solid var(--brand-red); border-radius: 2px; font-family: "Merriweather", Georgia, serif; font-weight: 700; font-size: 11px; color: var(--brand-red); text-decoration: none; display: flex; align-items: center; justify-content: center; }
  .intro-actions a.is-primary { background: var(--brand-red); color: var(--white); }
  .intro-frame { position: absolute; left: 496px; top: 73px; width: 297px; height: 260px; background: var(--brand-red); }
  .intro-photo { position: absolute; left: 487px; top: 64px; width: 297px; height: 260px; background: radial-gradient(circle at 40% 45%, #d9b25a 0%, #b5452d 45%, #7e1f1c 80%, #4a2a22 100%); }

  .site-footer { position: absolute; left: 0; top: 931px; width: 894px; height: 269px; background: var(--black); color: var(--white); }
  .footer-brand { position: absolute; left: 83px; top: 43px; width: 99px; height: 84px; display: flex; align-items: center; justify-content: center; }
  .footer-brand .brand-name { font-family: "Merriweather", Georgia, serif; font-weight: 900; font-size: 15px; line-height: 1.2; color: var(--white); text-align: center; }
  .social-links a { position: absolute; top: 150px; width: 28px; height: 28px; border-radius: 50%; background: var(--white); color: var(--brand-red); font-size: 7px; font-weight: 600; text-decoration: none; display: flex; align-items: center; justify-content: center; }
  .social-links a.is-active { background: var(--brand-red); color: var(--white); }
  .footer-divider { position: absolute; left: 290px; top: 52px; width: 1px; height: 132px; background: var(--footer-rule); }
  .footer-col { position: absolute; top: 48px; }
  .footer-col h3 { font-family: "Poppins", Arial, sans-serif; font-weight: 600; font-size: 15px; margin-bottom: 9px; }
  .footer-col li { list-style: none; font-size: 11.5px; line-height: 19.2px; display: flex; align-items: center; gap: 9px; }
  .footer-col li svg { flex: none; }
  .contact-item { position: absolute; left: 0; display: flex; gap: 7px; font-size: 11.5px; line-height: 19px; white-space: nowrap; }
  .contact-item svg { flex: none; margin-top: 3px; }
  .footer-rule { position: absolute; left: 83px; top: 209px; width: 728px; height: 1px; background: var(--footer-rule); }
  .copyright { position: absolute; left: 0; top: 226px; width: 894px; text-align: center; font-size: 11.5px; }
</style>
</head>
<body>

<header class="site-header">
  <nav class="main-nav">
    <a class="is-active" href="#" style="left:83px">HOME</a>
    <a href="#" style="left:148px">THE KITCHEN</a>
    <a href="#" style="left:253px">OUR BEERS</a>
    <a href="#" style="left:566px">VISIT US</a>
    <a href="#" style="left:645px">ABOUT US</a>
    <a href="#" style="left:732px">MERCH</a>
  </nav>
  <svg class="search-icon" width="14" height="14" viewBox="0 0 14 14" aria-label="Search">
    <circle cx="5.8" cy="5.8" r="4.4" fill="none" stroke="var(--brand-red)" stroke-width="2"/>
    <line x1="9" y1="9" x2="13" y2="13" stroke="var(--brand-red)" stroke-width="2.4" stroke-linecap="round"/>
  </svg>
</header>

<div class="brand-tab"><span class="brand-name">Lantern<br>Hollow</span></div>

<section class="hero">
  <div class="hero-photo" role="img" aria-label="Square pepperoni pizza on a cooling rack beside glasses of beer on a red wooden table"></div>
  <div class="hero-panel"></div>
  <div class="promo-badge" role="img" aria-label="Yellow starburst promo badge reading Try Zesty">TRY ZESTY!</div>
  <h1 class="hero-title">SQUARE PIZZA AND GREAT BEER IN PORTLAND, MAINE</h1>
  <div class="hero-actions">
    <a class="is-primary" href="#" style="left:493px;width:82px">Order Pizza</a>
    <a href="#" style="left:582px;width:69px">Visit Us</a>
    <a href="#" style="left:660px;width:73px">Our Beers</a>
    <a href="#" style="left:741px;width:69px">About Us</a>
  </div>
  <div class="slider-dots">
    <span style="top:191px"></span>
    <span style="top:210px"></span>
    <span class="is-current" style="top:229px"></span>
    <span style="top:248px"></span>
  </div>
</section>

<section class="intro">
  <h2 class="intro-title">What is Detroit-style pizza?</h2>
  <p class="intro-text">Lorem ipsum dolor sit amet, consectetur adipiscing elit, sed do eiusmod tempor incididunt ut labore et dolore magna aliqua. Ut enim ad minim veniam, quis nostrud exercitation ullamco laboris nisi ut aliquip ex ea commodo consequat. Duis aute irure dolor in reprehenderit in voluptate velit esse cillum dolore eu fugiat nulla pariatur. Excepteur sint occaecat cupidatat non proident, sunt in culpa qui officia deserunt mollit anim id est laborum.</p>
  <div class="intro-actions">
    <a class="is-primary" href="#" style="left:83px;width:90px">Order Online</a>
    <a href="#" style="left:183px;width:102px">View full Menu</a>
  </div>
  <div class="intro-frame"></div>
  <div class="intro-photo" role="img" aria-label="Overhead view of a Detroit-style pepperoni pizza topped with green onions on a wire rack"></div>
</section>

<footer class="site-footer">
  <div class="footer-brand"><span class="brand-name">Lantern<br>Hollow</span></div>
  <nav class="social-links" aria-label="Social media links">
    <a class="is-active" href="#" style="left:83px">Nook</a>
    <a href="#" style="left:115px">Chirp</a>
    <a href="#" style="left:147px">Wren</a>
    <a href="#" style="left:179px">Lens</a>
  </nav>
  <div class="footer-divider"></div>

  <div class="footer-col" style="left:322px">
    <h3>Quick Links</h3>
    <ul>
      <li><svg width="9" height="8" viewBox="0 0 9 8"><path d="M1 1l3 3-3 3M5 1l3 3-3 3" fill="none" stroke="#fff" stroke-width="1.2"/></svg>Home</li>
      <li><svg width="9" height="8" viewBox="0 0 9 8"><path d="M1 1l3 3-3 3M5 1l3 3-3 3" fill="none" stroke="#fff" stroke-width="1.2"/></svg>The Kitchen</li>
      <li><svg width="9" height="8" viewBox="0 0 9 8"><path d="M1 1l3 3-3 3M5 1l3 3-3 3" fill="none" stroke="#fff" stroke-width="1.2"/></svg>Our Beers</li>
      <li><svg width="9" height="8" viewBox="0 0 9 8"><path d="M1 1l3 3-3 3M5 1l3 3-3 3" fill="none" stroke="#fff" stroke-width="1.2"/></svg>Visit Us</li>
      <li><svg width="9" height="8" viewBox="0 0 9 8"><path d="M1 1l3 3-3 3M5 1l3 3-3 3" fill="none" stroke="#fff" stroke-width="1.2"/></svg>About Us</li>
      <li><svg width="9" height="8" viewBox="0 0 9 8"><path d="M1 1l3 3-3 3M5 1l3 3-3 3" fill="none" stroke="#fff" stroke-width="1.2"/></svg>Merch</li>
    </ul>
  </div>

  <div class="footer-col" style="left:476px">
    <h3>Our Company</h3>
    <ul>
      <li><svg width="9" height="8" viewBox="0 0 9 8"><path d="M1 1l3 3-3 3M5 1l3 3-3 3" fill="none" stroke="#fff" stroke-width="1.2"/></svg>Terms &amp; Conditions</li>
      <li><svg width="9" height="8" viewBox="0 0 9 8"><path d="M1 1l3 3-3 3M5 1l3 3-3 3" fill="none" stroke="#fff" stroke-width="1.2"/></svg>Privacy Policy</li>
      <li><svg width="9" height="8" viewBox="0 0 9 8"><path d="M1 1l3 3-3 3M5 1l3 3-3 3" fill="none" stroke="#fff" stroke-width="1.2"/></svg>About Us</li>
      <li><svg width="9" height="8" viewBox="0 0 9 8"><path d="M1 1l3 3-3 3M5 1l3 3-3 3" fill="none" stroke="#fff" stroke-width="1.2"/></svg>Support</li>
    </ul>
  </div>

  <div class="footer-col" style="left:637px;width:220px;height:150px">
    <h3>Contact us</h3>
    <div class="contact-item" style="top:30px">
      <svg width="10" height="13" viewBox="0 0 10 13"><path d="M5 0a5 5 0 0 0-5 5c0 3.5 5 8 5 8s5-4.5 5-8a5 5 0 0 0-5-5z" fill="#fff"/><circle cx="5" cy="5" r="1.8" fill="#000"/></svg>
      <span>48 Millrace Lane #3<br>Portland, ME 04102</span>
    </div>
    <div class="contact-item" style="top:80px">
      <svg width="12" height="12" viewBox="0 0 12 12"><path d="M2.5 0.5l2 2.6-1.2 1.6c.8 1.7 2.2 3.1 3.9 3.9l1.6-1.2 2.6 2-1.1 2.1C5.2 11.6.4 6.8.4 1.6z" fill="#fff"/></svg>
      <span>1+ (555) 014 2290</span>
    </div>
    <div class="contact-item" style="top:111px">
      <svg width="13" height="10" viewBox="0 0 13 10"><rect x="0" y="0" width="13" height="10" rx="1" fill="#fff"/><path d="M0.5 1l6 4.5 6-4.5" fill="none" stroke="#000" stroke-width="1.2"/></svg>
      <span>beerme@lanternhollowbrew.example</span>
    </div>
  </div>

  <div class="footer-rule"></div>
  <p class="copyright">©Copyrights 2022 Lanternhollowbrew &nbsp;|&nbsp;&nbsp; All Rights Reserved</p>
</footer>

</body>
</html>
```